Talbrook Answering Service Brochure

Design a brochure for an answering service/call center based on the information submitted/attached. Photos and text will be included. Would like it designed to complement the logo provided. This brochure will explain to the potential customer who we are and what we have to offer.

The Talbrook representatives take and processes inbound calls, 24-7-365

Target Market(s)

Any business, however, primarily Medical, oil and gas, non profits, and the service industry

Industry/Entity Type

Telecommunications

Font styles to use
Serif
Other font styles liked:
• coordinate with logo

Requirements
Must have
• Modern, bright, bold and neatly structured brochure that will complement the logo and our brand.

```html
<!DOCTYPE html>
<html lang="en">
<head>
<meta charset="utf-8">
<title>Talbrook Answering Service Brochure</title>
<link href="https://fonts.googleapis.com/css2?family=Poppins:wght@600&family=Questrial&display=swap" rel="stylesheet">
<style>
  :root {
    --stage: #a8a8a8;
    --charcoal: #333233;
    --charcoal-deep: #2a292a;
    --brand-red: #d6141f;
    --paper: #ffffff;
    --ink: #3a3a3a;
    --photo-light: #eef1f4;
    --photo-mid: #cfd6dd;
    --photo-warm: #b89a86;
  }
  * { box-sizing: border-box; margin: 0; padding: 0; }
  html, body { width: 1200px; height: 978px; overflow: hidden; }
  body { background: var(--stage); font-family: "Questrial", sans-serif; position: relative; }

  .brochure { position: absolute; left: 107px; top: 130px; width: 993px; height: 708px; background: var(--paper); }
  .brochure__art { position: absolute; inset: 0; }

  .panel-back { position: absolute; left: 0; top: 0; width: 498px; height: 708px; color: var(--paper); }
  .contact { position: absolute; left: 0; top: 356px; width: 498px; text-align: center; }
  .contact__title { font-family: "Poppins", sans-serif; font-weight: 600; font-size: 21px; display: inline-block; padding: 0 28px 4px; border-bottom: 1.5px solid #d9d9d9; }
  .contact__phones { list-style: none; margin-top: 8px; font-size: 13px; line-height: 21px; }
  .contact__web { display: inline-block; margin-top: 6px; background: var(--brand-red); border-radius: 3px; padding: 2px 14px; font-size: 15px; letter-spacing: .3px; width: 191px; }
  .contact__tagline { margin-top: 8px; font-size: 13.5px; }

  .phone-icon { display: inline-block; width: 10px; height: 10px; vertical-align: -1px; margin-right: 5px; }

  .panel-front { position: absolute; left: 498px; top: 0; width: 495px; height: 708px; }
  .wordmark { position: absolute; left: 25px; top: 436px; display: flex; align-items: center; gap: 10px; font-family: "Poppins", sans-serif; font-weight: 600; font-size: 17px; line-height: 19px; color: var(--ink); letter-spacing: .5px; }
  .wordmark__dot { width: 30px; height: 30px; border-radius: 50%; background: var(--brand-red); }
  .intro { position: absolute; left: 25px; top: 536px; width: 445px; font-size: 13.5px; line-height: 17px; color: var(--ink); text-align: justify; }
  .promise { position: absolute; left: 25px; top: 607px; width: 246px; color: var(--brand-red); font-size: 14px; border-bottom: 1.5px solid var(--brand-red); padding-bottom: 1px; }
  .front-phones { position: absolute; left: 25px; top: 633px; list-style: none; font-size: 13px; line-height: 17px; color: var(--ink); }
  .front-phones .area { color: var(--brand-red); }

  .footer-band { position: absolute; left: 0; bottom: 8px; width: 993px; height: 20px; background: var(--brand-red); display: flex; }
  .footer-band__url { width: 498px; text-align: center; color: var(--paper); font-size: 13px; line-height: 20px; letter-spacing: .3px; }
</style>
</head>
<body>
  <main class="brochure">
    <svg class="brochure__art" width="993" height="708" viewBox="0 0 993 708" aria-hidden="false">
      <defs>
        <linearGradient id="photoTone" x1="0" y1="0" x2="1" y2="0.4">
          <stop offset="0" stop-color="var(--photo-light)"/>
          <stop offset="0.45" stop-color="var(--photo-mid)"/>
          <stop offset="0.75" stop-color="var(--photo-warm)"/>
          <stop offset="1" stop-color="var(--photo-light)"/>
        </linearGradient>
        <radialGradient id="backSheen" cx="0.2" cy="0.8" r="0.9">
          <stop offset="0" stop-color="var(--charcoal)"/>
          <stop offset="1" stop-color="var(--charcoal-deep)"/>
        </radialGradient>
      </defs>
      <rect class="back-fill" x="0" y="0" width="498" height="708" fill="url(#backSheen)"/>
      <path class="hero-photo" role="img" aria-label="Photo of smiling call centre agents wearing headsets in a bright office"
            d="M228,0 L993,0 L993,460 C850,440 640,390 498,292 C420,235 330,80 228,0 Z" fill="url(#photoTone)"/>
      <path class="curve-shade" d="M498,300 C640,402 850,458 993,480 L993,466 C850,446 640,394 498,294 Z" fill="var(--charcoal)"/>
      <path class="curve-accent" d="M228,0 C330,80 420,235 498,292 C640,390 850,440 993,460" fill="none" stroke="var(--brand-red)" stroke-width="5"/>
      <path class="curve-accent-wide" d="M700,385 C820,430 900,448 993,458 L993,472 C900,462 820,444 700,392 Z" fill="var(--brand-red)"/>
    </svg>

    <section class="panel-back">
      <div class="contact">
        <h2 class="contact__title">Contact Us:</h2>
        <ul class="contact__phones">
          <li><svg class="phone-icon" viewBox="0 0 10 10"><rect width="10" height="10" rx="2" fill="#fff"/><path d="M3 2.2 L4.2 3.6 L3.6 4.3 Q4.5 5.8 5.7 6.4 L6.4 5.8 L7.8 7 L7 8 Q3.5 7.2 2 3 Z" fill="#333"/></svg>(866) 555-0142</li>
          <li><svg class="phone-icon" viewBox="0 0 10 10"><rect width="10" height="10" rx="2" fill="#fff"/><path d="M3 2.2 L4.2 3.6 L3.6 4.3 Q4.5 5.8 5.7 6.4 L6.4 5.8 L7.8 7 L7 8 Q3.5 7.2 2 3 Z" fill="#333"/></svg>(409) 555-0187</li>
        </ul>
        <div class="contact__web">www. Talbrooksvc.com</div>
        <p class="contact__tagline">to subscribe to a Great Service, and a Strong ROI!</p>
      </div>
    </section>

    <section class="panel-front">
      <div class="wordmark">
        <span class="wordmark__dot"></span>
        <span class="wordmark__name">TALBROOK<br>ANSWERING SERVICE</span>
      </div>
      <p class="intro">Talbrook Answering Service is your award winning, five start center, backed by critical redundancy and a solid infrastructure, for the highest availability possible.</p>
      <p class="promise">Any Call - Any Time - Any Place</p>
      <ul class="front-phones">
        <li><svg class="phone-icon" viewBox="0 0 10 10"><rect width="10" height="10" rx="2" fill="#d6141f"/><path d="M3 2.2 L4.2 3.6 L3.6 4.3 Q4.5 5.8 5.7 6.4 L6.4 5.8 L7.8 7 L7 8 Q3.5 7.2 2 3 Z" fill="#fff"/></svg><span class="area">(866)</span> 555-0142</li>
        <li><svg class="phone-icon" viewBox="0 0 10 10"><rect width="10" height="10" rx="2" fill="#d6141f"/><path d="M3 2.2 L4.2 3.6 L3.6 4.3 Q4.5 5.8 5.7 6.4 L6.4 5.8 L7.8 7 L7 8 Q3.5 7.2 2 3 Z" fill="#fff"/></svg><span class="area">(409)</span> 555-0187</li>
      </ul>
    </section>

    <footer class="footer-band">
      <span class="footer-band__url">www. Talbrooksvc.com</span>
      <span class="footer-band__url">www. Talbrooksvc.com</span>
    </footer>
  </main>
</body>
</html>
```